We need 3 A2 posters similar look but different enough to be eye catching when changed.

We are a healthcare centre that requires 3 A2 posters - simple, similar but different background colours. These posters will be used within our business to promote services we provide to our clients.

The design should include our logo(attached), a large header and a large section in the middle of the poster to promote the event. We need a blank text box (which WE can insert text to advertise), and 1 image to advertise the event. Please note, we do not need you to choose an image we simply would like you to place a demo to give us an idea of where it should sit.

We want to use the bubble design (attached) as a background and the company colours pink, orange and blue - as on our website. Attached is a copy of our logo and background bubble effect. You can also refer to our website - www.tallowbrookwellness.com.au for more inspiration.

Just to reiterate, these posters should be simple, different but have a uniform feel. They should have an empty middle section that can be edited to add text and a space for an eye catching title and matching image.

Our services include Chiropractic, Podiatry, Nutrition, Massage, Yoga, Pilates and Specialised rehabilitation classes.

Reason: Hi designers, I know we are all busy but I really need more designs from the designers I invited to this project and look forward to receiving more designs. Any questions please let me know. Regards, Marion

Reason: Hi all Increased the budget Regards Marion

Corporate Sydney City office workers

Healthcare

• logo and company colours
section in the middles that can be edited to add text
Space allocated for image placement
Catchy title/header

```html
<!DOCTYPE html>
<html lang="en">
<head>
<meta charset="utf-8">
<title>Tallowbrook Wellness – Introducing</title>
<link rel="stylesheet" href="https://fonts.googleapis.com/css2?family=Roboto:wght@700&family=Cinzel:wght@700&family=Courgette&display=swap">
<style>
  :root {
    --pink: #c8519a;
    --pink-soft: #e19bc6;
    --orange: #e9a55e;
    --orange-light: #f6c592;
    --orange-deep: #ef9b45;
    --lavender: #a9a9d6;
    --blue: #5f5fae;
    --ink: #4b4a98;
    --grey-bg: #e4e4e4;
    --black: #111111;
    --white: #ffffff;
    --pill: #c85a86;
  }
  * { box-sizing: border-box; margin: 0; padding: 0; }
  html, body { width: 848px; height: 1200px; overflow: hidden; background: var(--white); }
  .poster { position: relative; width: 848px; height: 1200px; overflow: hidden; background: var(--white); }
  .bubble-field {
    position: absolute; inset: 160px 0 0 0;
    background: radial-gradient(ellipse at 60% 45%, #dcdcdc 0%, var(--grey-bg) 45%, #f2f2f2 100%);
  }
  .sweep { position: absolute; inset: 0; }
  .header { position: absolute; left: 0; top: 0; width: 848px; height: 150px; background: var(--lavender); }
  .header .block-pink { position: absolute; left: 0; top: 0; width: 140px; height: 150px; background: var(--pink-soft); }
  .header .block-orange { position: absolute; left: 140px; top: 0; width: 62px; height: 150px; background: var(--orange); }
  .header .band { position: absolute; left: 0; top: 42px; width: 848px; height: 62px; background: var(--blue); opacity: .95; }
  .brand-name {
    position: absolute; left: 20px; top: 56px;
    font: 700 26px/34px "Roboto", Arial, sans-serif; color: var(--white);
  }
  .rule { position: absolute; left: 14px; top: 151px; width: 834px; height: 8px; background: var(--black); }
  .headline {
    position: absolute; left: 60px; top: 188px;
    font: 700 56px/1 "Cinzel", Georgia, serif; color: var(--ink);
    letter-spacing: 1px; text-shadow: 3px 3px 0 rgba(0,0,0,.45);
  }
  .services { position: absolute; left: 0; top: 268px; list-style: none; }
  .services li { font: 29px/1 "Courgette", cursive; color: var(--ink); margin-bottom: 28px; white-space: nowrap; }
  .services li:nth-child(1) { padding-left: 90px; }
  .services li:nth-child(2) { padding-left: 110px; }
  .services li:nth-child(3) { padding-left: 144px; }
  .text-box {
    position: absolute; left: 24px; top: 1055px; width: 800px; height: 125px;
    border-radius: 63px; background: linear-gradient(90deg, var(--pill), #d07ab2); opacity: .85;
  }
</style>
</head>
<body>
<div class="poster">
  <div class="bubble-field" role="img" aria-label="Soft grey rounded-bubble background pattern"></div>

  <svg class="sweep" width="848" height="1200" viewBox="0 0 848 1200" aria-hidden="true">
    <path d="M0 140 Q 470 430 820 1200 L0 1200 Z" fill="var(--orange-light)" opacity=".85"/>
    <path d="M0 330 Q 330 650 560 1200 L0 1200 Z" fill="var(--orange)" opacity=".55"/>
    <path d="M0 620 Q 200 860 330 1200 L0 1200 Z" fill="var(--orange-deep)" opacity=".6"/>
  </svg>

  <header class="header">
    <div class="block-pink"></div>
    <div class="block-orange"></div>
    <div class="band"></div>
    <span class="brand-name">Tallowbrook Wellness</span>
  </header>
  <div class="rule"></div>

  <h1 class="headline">INTRODUCING</h1>
  <ul class="services">
    <li>Nutritional Assessments (by The Nutritionist)</li>
    <li>Foot And Gait Assessments (podiatrist)</li>
    <li>Chiropractic Spinal Health Checks</li>
  </ul>

  <div class="text-box"></div>
</div>
</body>
</html>
```